TWPC Business Card Design

Business card for sole operator professional civil and traffic engineer.
Clients are developers and planners who require assistance with traffic strategic master planning advice and design development for access and infrastructure associated with the development.
Colours already in use are greens for the business name and black for other legend. The attached file shows the letterhead template which is currently in use.
Target Market(s)
Professional Clients in development industry
Most clients known to the Principal and card is mostly required to allow ongoing contact
Industry/Entity Type
Business
Contact Information for Business Card
LACHLAN PETTIGREW CONSULTING PARTNERS
ABN 37 814 529 106
PO Box 418 KELWOOD NSW 2619
Lachlan Pettigrew 0412 358 971
l.pettigrew@corvanmail.net

```html
<!DOCTYPE html>
<html lang="en">
<head>
<meta charset="utf-8">
<title>TWPC Business Card</title>
<link href="https://fonts.googleapis.com/css2?family=Patrick+Hand&family=Arimo:wght@400&display=swap" rel="stylesheet">
<style>
  :root {
    --card-black: #050505;
    --brand-green: #8fc73e;
    --band-green: #97c93d;
    --text-white: #f2f2f2;
    --backdrop: #d8d3cb;
  }
  html, body {
    margin: 0;
    padding: 0;
    width: 1200px;
    height: 800px;
    overflow: hidden;
    background: var(--backdrop);
  }
  .canvas {
    position: relative;
    width: 1200px;
    height: 800px;
  }
  .card {
    position: absolute;
    left: 100px;
    top: 95px;
    width: 1000px;
    height: 610px;
    background: var(--card-black);
    border-radius: 14px;
    overflow: hidden;
    box-shadow: 0 18px 40px rgba(0,0,0,0.25);
  }
  .side-band {
    position: absolute;
    left: 0;
    top: 0;
    width: 205px;
    height: 100%;
    background: var(--band-green);
  }
  .name-tab {
    position: absolute;
    left: 135px;
    top: 62px;
    width: 120px;
    height: 100px;
    background: var(--card-black);
    border-radius: 50px 0 0 50px;
  }
  .business-name {
    position: absolute;
    left: 182px;
    top: 86px;
    width: 780px;
    margin: 0;
    font-family: "Patrick Hand", cursive;
    font-weight: 400;
    font-size: 39px;
    line-height: 1.2;
    letter-spacing: 2px;
    color: var(--brand-green);
    white-space: nowrap;
  }
  .person-name {
    position: absolute;
    left: 290px;
    top: 200px;
    margin: 0;
    font-family: "Arimo", sans-serif;
    font-weight: 400;
    font-size: 40px;
    color: var(--text-white);
  }
  .contact-list {
    position: absolute;
    left: 222px;
    top: 300px;
    margin: 0;
    padding: 0;
    list-style: none;
    font-family: "Arimo", sans-serif;
    font-size: 28px;
    color: var(--text-white);
  }
  .contact-item {
    display: flex;
    align-items: center;
    height: 42px;
  }
  .contact-icon {
    width: 26px;
    height: 26px;
    margin-right: 22px;
    flex: none;
    fill: var(--brand-green);
  }
</style>
</head>
<body>
<div class="canvas">
  <div class="card">
    <div class="side-band"></div>
    <div class="name-tab"></div>
    <h1 class="business-name">LACHLAN PETTIGREW CONSULTING PARTNERS</h1>
    <p class="person-name">Lachlan Pettigrew</p>
    <ul class="contact-list">
      <li class="contact-item">
        <svg class="contact-icon" viewBox="0 0 24 24" aria-hidden="true"><path d="M2 7c0-2 4-4 10-4s10 2 10 4v2h-5V7H7v2H2z"/><path d="M6 11h12l3 9H3z"/><circle cx="12" cy="15" r="2.5" fill="#050505"/></svg>
        <span>0412 358 971</span>
      </li>
      <li class="contact-item">
        <svg class="contact-icon" viewBox="0 0 24 24" aria-hidden="true"><path d="M12 2a7 7 0 0 0-7 7c0 5 7 13 7 13s7-8 7-13a7 7 0 0 0-7-7zm0 10a3 3 0 1 1 0-6 3 3 0 0 1 0 6z"/></svg>
        <span>ABN 37 814 529 106</span>
      </li>
      <li class="contact-item">
        <svg class="contact-icon" viewBox="0 0 24 24" aria-hidden="true"><path d="M12 3 1 12h3v9h6v-6h4v6h6v-9h3z"/></svg>
        <span>PO Box 418 KELWOOD NSW 2619</span>
      </li>
      <li class="contact-item">
        <svg class="contact-icon" viewBox="0 0 24 24" aria-hidden="true"><path d="M2 5h20v14H2z"/><path d="M2 5l10 8 10-8" fill="none" stroke="#050505" stroke-width="2"/></svg>
        <span>l.pettigrew@corvanmail.net</span>
      </li>
    </ul>
  </div>
</div>
</body>
</html>
```